Business Card and Letterhead for Pimlu - modern real estate business

I need a double sided business card design for Pimlu. Please see business card brief here https://files.trelvonadocs.com/sheet/r/7QzTmWbaXLJnoPEd-kRyUgFhHsstbvCe2qfoMxDa_pz/view?mode=shared

Please feel free to design the business cards however you feel best. I am happy to give some creative freedoms and then provide feedback from there.

Please then also create a letterhead to match the business card design

Colors

Designer to choose colors to be used in the design.

Requirements
Must have
• Must be a modern, elegant business card which looks very professional

```html
<!DOCTYPE html>
<html lang="en">
<head>
<meta charset="utf-8">
<title>Pimlu – Business Card</title>
<link href="https://fonts.googleapis.com/css2?family=Roboto:wght@400;500;700&display=swap" rel="stylesheet">
<style>
  :root {
    --page: #e9e6e2;
    --card-dark: #1c1c1d;
    --card-mid: #2c2c2e;
    --card-light: #3d3d40;
    --band: #121213;
    --red: #e3202b;
    --white: #f4f4f4;
    --silver: #c9c9cc;
  }
  * { box-sizing: border-box; margin: 0; padding: 0; }
  html, body {
    width: 1200px; height: 960px; overflow: hidden;
    background: var(--page);
    font-family: "Roboto", Arial, sans-serif;
  }
  .sheet {
    position: relative; width: 1200px; height: 960px;
    display: flex; flex-direction: column; align-items: center;
    justify-content: center; gap: 60px;
  }
  .card {
    position: relative; width: 700px; height: 400px;
    overflow: hidden; border-radius: 4px;
    box-shadow: 0 10px 28px rgba(0,0,0,.25);
  }

  /* Back */
  .card--back {
    background: var(--card-dark);
    display: flex; align-items: center; justify-content: center;
  }
  .back-wordmark {
    color: var(--silver); font-weight: 500;
    font-size: 96px; letter-spacing: 10px;
  }

  /* Front */
  .card--front {
    background: radial-gradient(ellipse at 70% 35%, var(--card-light) 0%, var(--card-mid) 40%, var(--card-dark) 100%);
  }
  .name-band {
    position: absolute; left: 0; top: 52px; width: 470px; height: 84px;
    background: linear-gradient(90deg, var(--band) 70%, rgba(18,18,19,0) 100%);
  }
  .portrait {
    position: absolute; right: 0; top: 0; width: 290px; height: 400px;
    background: linear-gradient(180deg, #4a4a4d 0%, #3a3a3d 45%, #2a2a2c 100%);
  }
  .details {
    position: absolute; left: 34px; top: 62px; width: 400px;
  }
  .agent-name {
    color: var(--red); font-weight: 700; font-size: 30px;
    letter-spacing: 1px; line-height: 1.1;
  }
  .agent-title {
    color: var(--white); font-size: 17px; margin-top: 4px;
  }
  .licence {
    color: var(--red); font-size: 16px; margin-top: 26px;
  }
  .contact-list { list-style: none; margin-top: 4px; }
  .contact-list li {
    display: flex; align-items: center; gap: 10px;
    color: var(--white); font-size: 16px; line-height: 1.45;
  }
  .contact-list svg { width: 13px; height: 13px; flex: none; }
  .agency { margin-top: 16px; padding-left: 52px; }
  .agency-wordmark {
    color: var(--red); font-weight: 500; font-size: 44px;
    letter-spacing: 4px; line-height: 1;
  }
  .agency .licence { margin-top: 4px; }
  .address { color: var(--red); font-size: 16px; margin-top: 2px; }
</style>
</head>
<body>
<main class="sheet">

  <section class="card card--back" aria-label="Card back">
    <span class="back-wordmark">PIMLU</span>
  </section>

  <section class="card card--front" aria-label="Card front">
    <div class="portrait" role="img" aria-label="Portrait photo of the agent in a dark suit"></div>
    <div class="name-band"></div>

    <div class="details">
      <h1 class="agent-name">DEAN MARLOW</h1>
      <p class="agent-title">Licenced Real Estate Agent</p>

      <p class="licence">Lic No. 31847206</p>
      <ul class="contact-list">
        <li>
          <svg viewBox="0 0 16 16" aria-hidden="true"><path fill="#e3202b" d="M3.6 1.5l2.3 2.6-1.3 1.9c.9 2 2.4 3.5 4.4 4.4l1.9-1.3 2.6 2.3-1.4 2.1C7 13.2 2.8 9 1.5 3z"/></svg>
          0400 318 552
        </li>
        <li>
          <svg viewBox="0 0 16 16" aria-hidden="true"><rect x="1" y="3" width="14" height="10" fill="#e3202b"/><path d="M1.5 3.5L8 9l6.5-5.5" stroke="#1c1c1d" stroke-width="1.4" fill="none"/></svg>
          dean@pimlu.com
        </li>
      </ul>

      <div class="agency">
        <p class="agency-wordmark">PIMLU</p>
        <p class="licence">Lic No. 40118293</p>
        <ul class="contact-list">
          <li>
            <svg viewBox="0 0 16 16" aria-hidden="true"><path fill="#e3202b" d="M3.6 1.5l2.3 2.6-1.3 1.9c.9 2 2.4 3.5 4.4 4.4l1.9-1.3 2.6 2.3-1.4 2.1C7 13.2 2.8 9 1.5 3z"/></svg>
            02 5550 1947
          </li>
          <li>
            <svg viewBox="0 0 16 16" aria-hidden="true"><rect x="1" y="3" width="14" height="10" fill="#e3202b"/><path d="M1.5 3.5L8 9l6.5-5.5" stroke="#1c1c1d" stroke-width="1.4" fill="none"/></svg>
            info@pimlu.com
          </li>
          <li>
            <svg viewBox="0 0 16 16" aria-hidden="true"><circle cx="8" cy="8" r="7" fill="#e3202b"/><path d="M1 8h14M8 1c-3 3.5-3 10.5 0 14M8 1c3 3.5 3 10.5 0 14" stroke="#1c1c1d" stroke-width="1.1" fill="none"/></svg>
            www.pimlu.com
          </li>
        </ul>
        <p class="address">PO Box 7316 Larkvale NSW 2790</p>
      </div>
    </div>
  </section>

</main>
</body>
</html>
```